Letterhead for a German Distribution/Manufacturing Company

We need a professional Letterhead in a unique Design.
not to playful.
The Letterhead has to show show that we are a international company with headquater in Germany.
all details like adress, Vat Tax Number, Bank Accout, Eori, email, Company number has to be on the Letterhead.
for example use: VAT TAX DE5470318 Bank Account: Kestrel Bank IBAN DE412058731ß204683 Swift: MORV0417352 EORI 3150428697 Company Number: HRB 51806 Adress: VOLMINTA UG Ahornweg 7 Postal Code 06384 City Kesselbach Country: Germany Email: info@volminta-example.com
the design can be colored but doesnt have to be
Industry/Entity Type
Manufacturing and international distribution
Requirements
Must have
- show that we are a international company with headquater in Germany. our company infos and logo

```html
<!DOCTYPE html>
<html lang="en">
<head>
<meta charset="utf-8">
<title>Volminta Letterhead</title>
<link rel="stylesheet" href="https://fonts.googleapis.com/css2?family=Arimo:wght@400;700&family=Questrial&display=swap">
<style>
  :root {
    --backdrop: #cbcacb;
    --paper: #ffffff;
    --ink: #4a4a4b;
    --ink-strong: #3f3f40;
    --rule: #6a6a6b;
    --band: #474748;
    --band-soft: #5a5a5b;
  }
  * { margin: 0; padding: 0; box-sizing: border-box; }
  html, body { width: 1173px; height: 1200px; overflow: hidden; background: var(--backdrop); }
  body { position: relative; font-family: "Arimo", Arial, sans-serif; color: var(--ink); }

  .letterhead {
    position: absolute; left: 230px; top: 96px; width: 714px; height: 1009px;
    background: var(--paper); box-shadow: 1px 2px 4px rgba(0,0,0,0.3); overflow: hidden;
  }

  .brand { position: absolute; left: 44px; top: 50px; height: 80px; display: flex; align-items: center; }
  .brand-dot { width: 50px; height: 50px; border-radius: 50%; background: var(--ink); margin-right: 14px; }
  .brand-name { font-size: 36px; font-weight: 700; color: var(--ink); letter-spacing: 0.5px; }

  .divider { position: absolute; top: 47px; width: 1px; height: 82px; background: var(--rule); }
  .divider.first { left: 334px; }
  .divider.second { left: 538px; }

  .company-facts { position: absolute; left: 351px; top: 44px; font-size: 11.6px; line-height: 14.2px; list-style: none; white-space: nowrap; }
  .company-facts b { color: var(--ink-strong); }

  .contact { position: absolute; left: 552px; top: 43px; font-size: 10.4px; line-height: 14.2px; white-space: nowrap; list-style: none; }
  .contact .address { margin-bottom: 3px; }
  .contact li { display: flex; align-items: center; }
  .contact svg { width: 9px; height: 9px; margin-right: 6px; fill: var(--ink); flex: none; }

  .header-rule { position: absolute; left: 44px; top: 139px; width: 625px; height: 1px; background: var(--rule); }

  .letter-body { position: absolute; left: 64px; top: 310px; width: 590px; }
  .salutation { font-family: "Questrial", Arial, sans-serif; font-size: 16.5px; font-weight: 700; color: var(--ink); margin-bottom: 27px; }
  .letter-body p.copy { font-size: 12.1px; line-height: 14.7px; margin-bottom: 12.5px; }
  .closing { font-size: 9.2px; font-weight: 700; margin-top: 22px; }
  .signature { width: 116px; height: 35px; margin-top: 29px; background: linear-gradient(90deg, #e6e6e6, #d6d6d6); border-radius: 3px; }

  .footer-band {
    position: absolute; left: 0; bottom: 0; width: 714px; height: 56px;
    background: linear-gradient(180deg, var(--band-soft), var(--band));
  }
</style>
</head>
<body>
  <main class="letterhead">
    <header>
      <div class="brand">
        <span class="brand-dot"></span>
        <span class="brand-name">VOLMINTA</span>
      </div>
      <span class="divider first"></span>
      <ul class="company-facts">
        <li><b>VAT TAX</b> DE5470318</li>
        <li><b>Bank Account:</b> Kestrel Bank</li>
        <li><b>IBAN</b> DE412058731ß204683</li>
        <li><b>Swift:</b> MORV0417352</li>
        <li><b>EORI</b> 3150428697</li>
        <li><b>Company Number:</b> HRB 51806</li>
      </ul>
      <span class="divider second"></span>
      <ul class="contact">
        <li class="address-line">Ahornweg 7</li>
        <li class="address-line">06384, Kesselbach</li>
        <li class="address-line address">Germany</li>
        <li><svg viewBox="0 0 10 10"><path d="M2 0.5 L3.6 2.8 L2.8 3.8 Q4 6.2 6.2 7.2 L7.2 6.4 L9.5 8 L8.3 9.5 Q3.5 9 0.5 1.7 Z"/></svg>555-318-0427</li>
        <li><svg viewBox="0 0 10 10"><path d="M0 2 H10 V8.5 H0 Z M0.8 2.6 L5 5.8 L9.2 2.6" stroke="#fff" stroke-width="0.8"/></svg>info@volminta-example.com</li>
        <li><svg viewBox="0 0 10 10"><circle cx="5" cy="5" r="4.8"/><path d="M3 2.5 L5 3.5 L4 5.5 L2 4.8 Z M6 5.5 L8 6 L6.8 8 L5.5 7.3 Z" fill="#fff"/></svg>www.volminta-example.com</li>
      </ul>
      <div class="header-rule"></div>
    </header>

    <section class="letter-body">
      <p class="salutation">Dear Mr. Harlow,</p>
      <p class="copy">Lorem ipsum dolor sit amet, consectetuer adipiscing elit, sed diam nonmmy nibh euismod tincidunt ut laor eet dolore magna aliquam erat volutpat. Ut wisi enim ad minim veniam, quis nostrud exerci tationmcorper suscipit lobortis nisl ut aliquip ex ea commodo consequat. Duis autem vel eum iriure dolor in hendrerit in vulputate velit esse molestie consequat, vel illum dolore eu feugiat</p>
      <p class="copy">Rorem ipsum dolor sit amet, consectetuer adipiscing elit, sed diam nonmmy nibh euismod tincidunt ut laor eet dolore magna aliquam erat volutpat. Ut wisi enim ad minim veniam, quis nostrud exerci tationmcorper suscipit lobortis nisl ut aliquip ex ea commodo consequat. Duis autem vel eum iriure dolor in hendrerit in vulputate velit esse molest</p>
      <p class="copy">Dorem ipsum dolor sit amet, consectetuer adipiscing elit, sed diam nonmmy nibh euismod tincidunt ut laor eet dolore magna aliquam erat volutpat. Ut wisi enim ad minim veniam, quis nostrud exerci tationmcorper suscipit lobortis nisl ut aliquip ex ea commodo consequat. Duis autem vel eum iriure dolor in hendrerit in suscipit lobortis nisl ut aliquip ex ea commodo consequat. Duis autem vel eum iriure dolor in hendrerit in vulputate velit esse molestie consequat, vel illum</p>
      <p class="copy">Sorem ipsum dolor sit amet, consectetuer adipiscing elit, sed diam nonmmy nibh euismod tincidunt ut laor eet dolore magna aliquam erat volutpat. Ut wisi enim ad minim veniam, quis nostrud exerci tationmcorper suscipit lobortis nisl ut aliquip ex ea commodo consequat. Duis autem vel eum iriure dolor in</p>
      <p class="closing">Sincerely,</p>
      <div class="signature" role="img" aria-label="Handwritten signature of the sender"></div>
    </section>

    <div class="footer-band" role="img" aria-label="Dark decorative footer band"></div>
  </main>
</body>
</html>
```